Roofing Contractor business card redesign

I want to redesign my business card with a fresh, eye catching concept

Target Market(s)

Residential Roofing Clients, potential employees, and subcontractors.

Industry/Entity Type

Business

Colors

Designer to choose colors to be used in the design.

Requirements
Nice to have
• I just want something that's more pleasing to the eye. You can use a combination of either / or of my logos.

```html
<!DOCTYPE html>
<html lang="en">
<head>
<meta charset="utf-8">
<title>Fair Deal Builders – Business Card</title>
<link href="https://fonts.googleapis.com/css2?family=Roboto+Condensed:wght@400;700&display=swap" rel="stylesheet">
<style>
  :root {
    --backdrop: #e7e2dc;
    --card-white: #fbfbfa;
    --maroon: #44130f;
    --brand-maroon: #4a1511;
    --accent-orange: #e8772e;
    --ink: #3a2b27;
    --rule: #b9b2ad;
    --on-dark: #ffffff;
  }
  * { margin: 0; padding: 0; box-sizing: border-box; }
  html, body { width: 1200px; height: 911px; overflow: hidden; }
  body {
    background: var(--backdrop);
    font-family: "Roboto Condensed", sans-serif;
    position: relative;
  }
  .card {
    position: absolute;
    width: 560px;
    height: 320px;
    border-radius: 18px;
    box-shadow: 0 10px 30px rgba(0,0,0,.18);
  }
  .card-front { left: 90px; top: 100px; background: var(--card-white); }
  .card-back  { left: 550px; top: 490px; background: var(--maroon); }

  .brand {
    position: absolute;
    display: flex;
    align-items: center;
    gap: 12px;
    font-weight: 700;
    white-space: nowrap;
  }
  .brand-dot { width: 34px; height: 34px; border-radius: 50%; flex: none; }
  .card-front .brand { right: 42px; top: 44px; font-size: 30px; color: var(--brand-maroon); }
  .card-front .brand-dot { background: var(--brand-maroon); }
  .card-back .brand { left: 50%; top: 50%; transform: translate(-50%, -60%); font-size: 38px; color: var(--on-dark); }
  .card-back .brand-dot { background: var(--on-dark); width: 42px; height: 42px; }

  .person { position: absolute; left: 40px; top: 150px; }
  .person-name { font-size: 19px; font-weight: 700; color: var(--ink); text-transform: uppercase; letter-spacing: .2px; }
  .person-title { font-size: 15px; color: var(--accent-orange); line-height: 1.3; }

  .contact-list { position: absolute; left: 40px; top: 218px; list-style: none; }
  .contact-list li { display: flex; align-items: center; gap: 9px; font-size: 14px; color: var(--ink); line-height: 19px; }
  .contact-list svg { width: 12px; height: 12px; fill: var(--ink); flex: none; }

  .divider { position: absolute; left: 262px; top: 222px; width: 1px; height: 70px; background: var(--rule); }
  .address { position: absolute; left: 280px; top: 226px; font-size: 14px; color: var(--ink); line-height: 19px; }

  .back-url {
    position: absolute; left: 0; right: 0; bottom: 44px;
    text-align: center; color: var(--on-dark);
    font-size: 13px; letter-spacing: 7px;
  }
</style>
</head>
<body>
  <section class="card card-front">
    <div class="brand"><span class="brand-dot"></span>Fair Deal Builders, Inc.</div>

    <div class="person">
      <div class="person-name">Sam Whitlock</div>
      <div class="person-title">Accredited Roof Inspector</div>
      <div class="person-title">Licensed Property Adjuster</div>
    </div>

    <ul class="contact-list">
      <li><svg viewBox="0 0 24 24"><path d="M6.6 10.8a15 15 0 0 0 6.6 6.6l2.2-2.2c.3-.3.7-.4 1-.2 1.1.4 2.3.6 3.6.6.6 0 1 .4 1 1V20c0 .6-.4 1-1 1A17 17 0 0 1 3 4c0-.6.4-1 1-1h3.5c.6 0 1 .4 1 1 0 1.3.2 2.5.6 3.6.1.3 0 .7-.2 1z"/></svg>(555) 210-4800</li>
      <li><svg viewBox="0 0 24 24"><path d="M3 3h18v18H3zM5 5v14h14V5z"/></svg>(555) 318-2290</li>
      <li><svg viewBox="0 0 24 24"><path d="M2 4h20v16H2zm2 2v.5l8 5 8-5V6zm0 3v9h16V9l-8 5z"/></svg>sam@fairdealtx.com</li>
      <li><svg viewBox="0 0 24 24"><path d="M12 2a10 10 0 1 0 0 20 10 10 0 0 0 0-20zm0 2c.9 0 2.2 1.8 2.8 5H9.2C9.8 5.8 11.1 4 12 4zM4.3 11h4.8a20 20 0 0 0 0 2H4.3a8 8 0 0 1 0-2zm6.8 0h1.8v2h-1.8zm3.8 0h4.8a8 8 0 0 1 0 2h-4.8a20 20 0 0 0 0-2zM9.2 15h5.6c-.6 3.2-1.9 5-2.8 5s-2.2-1.8-2.8-5z"/></svg>www.fairdealtx.com</li>
    </ul>

    <div class="divider"></div>
    <address class="address" style="font-style:normal">4810 Cedar Hollow Road Suite 12<br>Riverton, TX 75000</address>
  </section>

  <section class="card card-back">
    <div class="brand"><span class="brand-dot"></span>Fair Deal Builders, Inc.</div>
    <div class="back-url">www.fairdealtx.com</div>
  </section>
</body>
</html>
```